Gym Wall Story Feature-- Long Horizontal design for the full-width of the gym wall

We need a horizontal, LONG, story poster/display that artfully tells our gym's story using ALL of the attached information and photographs. I've also included where this display will go in our gym (aligned with, and under the trophies.) Please incorporate the color scheme of white, light grey, dark grey, and orange.

Thanks!

Target Market(s)

Upscale, exclusive, hip gym community

Industry/Entity Type

Gym

Font styles to use
Sans Serif

Colors
ffffff
000000
aaaaaa
5c5c5c
f78f20
e9e9e9

Requirements
Must have
• All images and text provided in the attachments. Clean, modern, design. MOSTLY white with just a couple pops of orange and light grey. text should be black or charcoal and easy to read. We would like to have our logo incorporated as well.
Nice to have
• Clean, stream-line look, nothing too busy or crowded.
Should not have
• Too busy, slanted lines, weird fonts, misalignment.

```html
<!DOCTYPE html>
<html lang="en">
<head>
<meta charset="utf-8">
<title>How Did The Tempo Start?</title>
<link href="https://fonts.googleapis.com/css2?family=Lato:wght@300;400;700;900&display=swap" rel="stylesheet">
<style>
  :root {
    --white: #ffffff;
    --black: #000000;
    --orange: #f78f20;
    --charcoal: #444444;
    --dark-grey: #5c5c5c;
    --mid-grey: #aaaaaa;
    --light-grey: #e9e9e9;
    --body-text: #6a6a6a;
  }
  html, body { margin: 0; padding: 0; overflow: hidden; background: var(--white); }
  .story {
    position: relative;
    width: 1200px;
    height: 546px;
    overflow: hidden;
    background: var(--white);
    font-family: "Lato", sans-serif;
  }
  .story > * { position: absolute; }
  .timeline-art { left: 0; top: 0; }
  .story-title {
    left: 118px; top: 58px; margin: 0;
    font-size: 20px; font-weight: 900; color: var(--orange); letter-spacing: 0.2px;
  }
  .photo {
    background: linear-gradient(160deg, #8a8a8a, #2e2e2e);
    border: 1px solid var(--charcoal);
  }
  .photo-early { left: 125px; top: 109px; width: 94px; height: 151px; background: linear-gradient(160deg, #bdbdbd, #3a3a3a); }
  .photo-comeback { left: 449px; top: 326px; width: 94px; height: 151px; background: linear-gradient(160deg, #c98a5a, #3a2418); }
  .photo-today { left: 773px; top: 109px; width: 94px; height: 151px; background: linear-gradient(160deg, #c9b79c, #2a2a2a); }
  .copy {
    margin: 0; font-size: 8.4px; line-height: 11.3px; color: var(--body-text); font-weight: 400;
  }
  .copy p { margin: 0 0 10px; }
  .copy .copy-strong { color: var(--black); font-weight: 700; }
  .copy-early { left: 235px; top: 100px; width: 190px; }
  .copy-comeback { left: 579px; top: 328px; width: 150px; }
  .copy-today { left: 884px; top: 100px; width: 182px; }
  .year {
    margin: 0; font-size: 20px; font-weight: 900; color: var(--orange);
  }
  .year-1973 { left: 95px; top: 308px; }
  .year-1981 { left: 419px; top: 262px; }
  .year-2015 { left: 744px; top: 305px; }
  .quote {
    left: 126px; top: 349px; width: 252px; height: 98px; margin: 0;
    display: flex; align-items: center; justify-content: center; text-align: center;
    color: var(--white); font-size: 14px; line-height: 17px; font-weight: 300;
  }
  .titles-heading {
    left: 884px; top: 156px; margin: 0;
    font-size: 10px; font-weight: 900; color: var(--orange);
  }
  .titles {
    left: 881px; top: 178px; width: 180px; margin: 0; padding: 0; list-style: none;
  }
  .title-row {
    display: flex; height: 15px; margin-bottom: 7.6px;
    font-size: 8.6px; font-weight: 700; color: var(--white); line-height: 15px;
  }
  .title-year { width: 28px; background: var(--orange); text-align: center; }
  .title-name { flex: 1; background: var(--dark-grey); text-align: center; }
  .exercise-icons { top: 282px; display: flex; gap: 13px; }
  .exercise-icons span { width: 27px; height: 29px; border-radius: 4px; background: var(--dark-grey); opacity: .85; }
  .icons-a { left: 189px; }
  .icons-b { left: 510px; }
  .icons-c { left: 839px; }
  .lifter-figure {
    left: 875px; top: 333px; width: 122px; height: 153px; border-radius: 6px;
    background: linear-gradient(180deg, #b8b8b8, #cfcfcf);
  }
</style>
</head>
<body>
<main class="story">
  <svg class="timeline-art" width="1200" height="546" viewBox="0 0 1200 546" aria-hidden="true">
    <g stroke="#f78f20" stroke-width="1.2" fill="none">
      <line x1="68" y1="296" x2="180" y2="296"/>
      <line x1="383" y1="296" x2="500" y2="296"/>
      <line x1="703" y1="296" x2="828" y2="296"/>
      <line x1="1038" y1="296" x2="1139" y2="296"/>
      <polyline points="118,260 118,296"/>
      <polyline points="442,296 442,464 449,464"/>
      <polyline points="766,296 766,143 773,143"/>
    </g>
    <g fill="#f78f20">
      <circle cx="118" cy="296" r="7"/>
      <circle cx="442" cy="296" r="7"/>
      <circle cx="766" cy="296" r="7"/>
      <circle cx="1090" cy="296" r="7"/>
    </g>
    <path d="M126 349 H428 L378 382 V447 H126 Z" fill="#444444"/>
  </svg>

  <h1 class="story-title">HOW DID THE TEMPO START?</h1>

  <div class="photo photo-early" role="img" aria-label="Black and white photo of young Garrett Vance posing as a competing bodybuilder"></div>
  <div class="copy copy-early">
    <p>The Tempo began with body builder and personal trainer, Garrett Vance. Garrett had a passion for fitness early on and opened his first gym in 1960. Shortly after, Garrett won Mr. Blue Ridge.</p>
    <p>Garrett's body-building career looked promising until one evening he was robbed and shot in the chest. As a result, Garrett suffered from nerve damage in the arm and figured at the age of 34, his weight lifting days were over.</p>
  </div>
  <p class="year year-1973">1973</p>

  <blockquote class="quote">“I thought I was through and<br>couldn’t continue lifting<br>but the tempo<br>changed everything,”</blockquote>

  <p class="year year-1981">1981</p>
  <div class="photo photo-comeback" role="img" aria-label="Colour photo of Garrett Vance on stage at a bodybuilding competition"></div>
  <div class="copy copy-comeback">
    <p>Garrett started with 2-pound weights and changed his whole training technique. No more bouncing or slinging, just steady and controlled movements. Through hard work and consistency, Garrett started shaping up his upper-body again.</p>
    <p class="copy-strong">Shortly after turning 40, Garrett won the National Mr. Continental competition.</p>
  </div>

  <p class="year year-2015">2015</p>
  <div class="photo photo-today" role="img" aria-label="Photo of Garrett Vance today standing in the gym in a black shirt"></div>
  <div class="copy copy-today">
    <p>Through his experiences, Garrett created The Tempo; a system that helps individuals develop a fundamentally sound workout regimen and accountability system.</p>
  </div>
  <h2 class="titles-heading">NATIONAL CHAMPIONSHIPS WON:</h2>
  <ul class="titles">
    <li class="title-row"><span class="title-year">1981</span><span class="title-name">Won Past 40 Mr. Continental</span></li>
    <li class="title-row"><span class="title-year">1999</span><span class="title-name">Won Past 60 Mr. Continental</span></li>
    <li class="title-row"><span class="title-year">1996</span><span class="title-name">Won Past 50 Mr. Continental</span></li>
    <li class="title-row"><span class="title-year">2009</span><span class="title-name">Won Past 70 Mr. Continental</span></li>
  </ul>

  <div class="exercise-icons icons-a" role="img" aria-label="Exercise pictograms: bike, push-up, pull-up, squat, run"><span></span><span></span><span></span><span></span><span></span></div>
  <div class="exercise-icons icons-b" role="img" aria-label="Exercise pictograms: bike, push-up, pull-up, squat, run"><span></span><span></span><span></span><span></span><span></span></div>
  <div class="exercise-icons icons-c" role="img" aria-label="Exercise pictograms: bike, push-up, pull-up, squat, run"><span></span><span></span><span></span><span></span><span></span></div>

  <div class="lifter-figure" role="img" aria-label="Grey silhouette of a man holding a barbell across his shoulders"></div>
</main>
</body>
</html>
```